I have a logo and need to design the business card and stationery.
Updates

The uploaded logo image named as GREYMARSH CONSTRUCTION which is to be replaced to GREYMARSH CONTRACTS. Kindly add below details and submit the designs- Company name- Greymarsh Engineering Contracts LLP Name & Post- Kelvan Joshi (Designated Partner) Address- Block No.317, Wing C, Tulvo Trade Court, Manek Pural Road, Ruparel Industrial Estate, Goregaon(E), Mumbai - 400 063 Contact- +91 97415 60382 Email- kelvanjoshi@mailbrook.example Website- www.greymarshcontracts.example Contact for Letterhead- +91-22-28754193

Hi Tovin Rahul, We are liking your Design #28860835. We have suggested some changes which are mentioned in feedback. Kindly revert with it asap to finalize this design.

Colors

Designer to choose colors to be used in the design.

```html
<!DOCTYPE html>
<html lang="en">
<head>
<meta charset="utf-8">
<title>Greymarsh Contracts – Business Card</title>
<link href="https://fonts.googleapis.com/css2?family=Poppins:wght@500;600&family=Hind:wght@400&display=swap" rel="stylesheet">
<style>
  :root {
    --backdrop: #b8b8b8;
    --card-white: #ffffff;
    --ink: #2a2a2a;
    --band: #2c2c2c;
    --shadow: #1e1e1e;
    --reverse-dark: #101010;
    --reverse-mid: #2e2e2e;
    --reverse-mark: #d9d9d9;
  }
  * { margin: 0; padding: 0; box-sizing: border-box; }
  html, body { width: 1200px; height: 801px; overflow: hidden; background: var(--backdrop); }
  .canvas { position: relative; width: 1200px; height: 801px; }

  .card { position: absolute; top: 274px; width: 443px; height: 263px; box-shadow: 3px 3px 0 var(--shadow); }
  .card-front { left: 153px; background: var(--card-white); color: var(--ink); overflow: hidden; }
  .card-back { left: 625px; overflow: hidden; }

  .top-band { position: absolute; left: 0; right: 0; top: 18px; height: 54px; background: var(--band); }
  .band-gap { position: absolute; left: 187px; width: 70px; top: 18px; height: 54px; background: var(--card-white); }
  .brand-square { position: absolute; left: 195px; top: 18px; width: 54px; height: 54px; background: var(--band); }
  .wordmark { position: absolute; left: 0; right: 0; top: 80px; text-align: center;
    font-family: "Poppins", sans-serif; font-weight: 600; font-size: 14px; line-height: 15px; letter-spacing: 1.5px; color: var(--ink); }

  .bottom-band { position: absolute; left: 0; right: 0; bottom: 0; height: 8px; background: var(--band); }
  .bottom-gap { position: absolute; left: 187px; width: 70px; bottom: 0; height: 8px; background: var(--card-white); }

  .person { position: absolute; left: 26px; top: 140px; }
  .person-name { font-family: "Poppins", sans-serif; font-weight: 500; font-size: 16px; letter-spacing: 0.2px; }
  .person-role { font-family: "Hind", sans-serif; font-size: 12.5px; margin-top: -2px; }

  .contacts { position: absolute; right: 22px; top: 130px; list-style: none; }
  .contacts li { display: flex; align-items: center; justify-content: flex-end; gap: 6px; height: 21px;
    font-family: "Hind", sans-serif; font-size: 12px; }
  .contacts svg { width: 17px; height: 17px; }

  .company { position: absolute; left: 0; right: 0; top: 198px; text-align: center; }
  .company-name { font-family: "Poppins", sans-serif; font-weight: 600; font-size: 15.5px; }
  .company-address { font-family: "Hind", sans-serif; font-size: 11px; line-height: 15px; margin-top: 2px; }

  .reverse-field { position: absolute; inset: 0;
    background: radial-gradient(ellipse at 70% 60%, var(--reverse-mid), var(--reverse-dark) 75%); }
  .reverse-mark { position: absolute; left: 895px; top: 443px; font-family: "Poppins", sans-serif;
    font-weight: 600; font-size: 13px; letter-spacing: 1.5px; color: var(--reverse-mark); }
</style>
</head>
<body>
<main class="canvas">
  <section class="card card-front">
    <div class="top-band"></div>
    <div class="band-gap"></div>
    <div class="brand-square"></div>
    <div class="wordmark">GREYMARSH<br>CONTRACTS</div>

    <div class="person">
      <p class="person-name">KELVAN JOSHI</p>
      <p class="person-role">Designated Partner</p>
    </div>

    <ul class="contacts">
      <li>+91 97415 60382
        <svg viewBox="0 0 17 17"><rect x="1" y="1" width="15" height="15" rx="2.5" fill="none" stroke="#2a2a2a" stroke-width="1.4"/><path d="M6 4.5c-1 .6-1.4 1.5-.9 3 .6 1.8 1.8 3.5 3.5 4.6 1.2.8 2.3.6 3-.3l-1.4-1.4-1 .6c-1-.6-1.9-1.6-2.4-2.8l.8-.8L6 4.5z" fill="#2a2a2a"/></svg>
      </li>
      <li>kelvanjoshi@mailbrook.example
        <svg viewBox="0 0 17 17"><rect x="1" y="1" width="15" height="15" rx="2.5" fill="none" stroke="#2a2a2a" stroke-width="1.4"/><rect x="4" y="5.5" width="9" height="6" fill="#2a2a2a"/><path d="M4 5.5l4.5 3.5 4.5-3.5M4 11.5l3.3-3M13 11.5l-3.3-3" fill="none" stroke="#fff" stroke-width=".8"/></svg>
      </li>
      <li>www.greymarshcontracts.example
        <svg viewBox="0 0 17 17"><rect x="1" y="1" width="15" height="15" rx="2.5" fill="none" stroke="#2a2a2a" stroke-width="1.4"/><circle cx="8.5" cy="8.5" r="4.5" fill="none" stroke="#2a2a2a" stroke-width="1"/><ellipse cx="8.5" cy="8.5" rx="2" ry="4.5" fill="none" stroke="#2a2a2a" stroke-width=".8"/><path d="M4 8.5h9M4.7 6.3h7.6M4.7 10.7h7.6" stroke="#2a2a2a" stroke-width=".7"/></svg>
      </li>
    </ul>

    <div class="company">
      <p class="company-name">Greymarsh Engineering Contracts LLP</p>
      <p class="company-address">Block No.317, Wing C, Tulvo Trade Court, Manek Pural Road,<br>Ruparel Industrial Estate, Goregaon(E), Mumbai - 400 063</p>
    </div>

    <div class="bottom-band"></div>
    <div class="bottom-gap"></div>
  </section>

  <section class="card card-back">
    <div class="reverse-field" role="img" aria-label="Dark repeating geometric brand pattern across the card back"></div>
  </section>
  <p class="reverse-mark">GREYMARSH</p>
</main>
</body>
</html>
```